Corvane Freight Company Business Card Design

We are a company that delivers natural saltwater (from the ocean) to aquarium companies, restaurants and home marine tanks. I would like a new business card to suit.

Must include Name, company name, abn, contact number and website as well as logo (see attached).

Looking for a design that stands out, has a clean but unique appearance.

Double and single sided entries welcome

Business

• Logo

```html
<!DOCTYPE html>
<html lang="en">
<head>
<meta charset="utf-8">
<title>Corvane Freight Company – Business Cards</title>
<link rel="stylesheet" href="https://fonts.googleapis.com/css2?family=Source+Sans+3:wght@400;600;700&display=swap">
<style>
  :root {
    --backdrop: #161616;
    --card-white: #ffffff;
    --sky: #53c9f2;
    --ocean: #0a5fad;
    --brand: #1a8fd0;
    --ink: #4a4a4a;
    --ink-on-sky: #1a5fa8;
    --font: "Source Sans 3", "Myriad Pro", Arial, sans-serif;
  }
  * { box-sizing: border-box; margin: 0; padding: 0; }
  html, body { width: 1200px; height: 750px; overflow: hidden; background: var(--backdrop); }
  body { position: relative; font-family: var(--font); }

  .card {
    position: absolute;
    width: 515px;
    height: 294px;
    background: var(--card-white);
    overflow: hidden;
  }
  .card--front-light { left: 73px;  top: 63px; }
  .card--front-dark  { left: 606px; top: 63px; }
  .card--back        { left: 342px; top: 409px; background: var(--sky); }

  .card__wave { position: absolute; inset: 0; width: 515px; height: 294px; }

  .brand {
    position: absolute;
    left: 0; right: 0;
    top: 44px;
    text-align: center;
    color: var(--brand);
    font-weight: 600;
    font-size: 30px;
    line-height: 1.05;
    letter-spacing: -0.3px;
  }
  .card--back .brand {
    top: 90px;
    color: var(--card-white);
    font-size: 54px;
    line-height: 1;
  }

  .holder {
    position: absolute;
    left: 0; right: 0;
    top: 166px;
    text-align: center;
    color: var(--ink);
    font-size: 15px;
  }
  .holder__name { font-weight: 700; font-size: 18px; }

  .contact {
    position: absolute;
    left: 0; right: 0;
    top: 222px;
    text-align: center;
    font-size: 13px;
    line-height: 23px;
    color: var(--ink-on-sky);
  }
  .card--front-dark .contact { top: 228px; color: var(--card-white); }
  .contact__row { display: flex; justify-content: center; align-items: center; gap: 18px; }
  .contact__item { display: inline-flex; align-items: center; gap: 6px; }
  .contact__icon { width: 11px; height: 11px; }
</style>
</head>
<body>

  <!-- Front, light band -->
  <section class="card card--front-light">
    <svg class="card__wave" viewBox="0 0 515 294" aria-hidden="true">
      <path d="M0 232 Q250 188 515 238 L515 294 L0 294 Z" fill="var(--sky)"/>
      <path d="M0 226 Q235 176 472 220 Q235 188 0 237 Z" fill="var(--ocean)"/>
    </svg>
    <div class="brand">Corvane Freight<br>Company</div>
    <div class="holder"><span class="holder__name">Your Name,</span> Title</div>
    <div class="contact">
      <div class="contact__row">
        <span class="contact__item">
          <svg class="contact__icon" viewBox="0 0 12 12"><path d="M3 1 L5 3.5 L4 5 Q5 7 7 8 L8.5 7 L11 9 L9.5 11 Q4 10.5 1 2.5 Z" fill="currentColor"/></svg>
          123-456-7892
        </span>
        <span class="contact__item">
          <svg class="contact__icon" viewBox="0 0 12 12"><circle cx="6" cy="6" r="5" fill="none" stroke="currentColor" stroke-width="1.2"/><path d="M1 6 H11 M6 1 Q3 6 6 11 M6 1 Q9 6 6 11" fill="none" stroke="currentColor" stroke-width="1"/></svg>
          www.corvanefreight.com
        </span>
      </div>
      <div>Street Name, City Name ,State, Zip Code</div>
      <div>ABN: 123456789</div>
    </div>
  </section>

  <!-- Front, dark band -->
  <section class="card card--front-dark">
    <svg class="card__wave" viewBox="0 0 515 294" aria-hidden="true">
      <path d="M0 238 Q250 196 515 240 L515 294 L0 294 Z" fill="var(--ocean)"/>
      <path d="M0 230 Q240 184 500 218 Q240 196 0 238 Z" fill="var(--sky)"/>
    </svg>
    <div class="brand">Corvane Freight<br>Company</div>
    <div class="holder"><span class="holder__name">Your Name,</span> Title</div>
    <div class="contact">
      <div class="contact__row">
        <span class="contact__item">
          <svg class="contact__icon" viewBox="0 0 12 12"><path d="M3 1 L5 3.5 L4 5 Q5 7 7 8 L8.5 7 L11 9 L9.5 11 Q4 10.5 1 2.5 Z" fill="currentColor"/></svg>
          123-456-7892
        </span>
        <span class="contact__item">
          <svg class="contact__icon" viewBox="0 0 12 12"><circle cx="6" cy="6" r="5" fill="none" stroke="currentColor" stroke-width="1.2"/><path d="M1 6 H11 M6 1 Q3 6 6 11 M6 1 Q9 6 6 11" fill="none" stroke="currentColor" stroke-width="1"/></svg>
          www.corvanefreight.com
        </span>
      </div>
      <div>Street Name, City Name ,State, Zip Code</div>
      <div>ABN: 123456789</div>
    </div>
  </section>

  <!-- Back -->
  <section class="card card--back">
    <div class="brand">Corvane Freight<br>Company</div>
  </section>

</body>
</html>
```